Personal training and nutrition business needs business card design

We need a business card that outlays our services and invites potential customers to join our team and take the first step to a healthier and more enjoyable life. We cater for any level of fitness and specialize in weight loss and conditioning, strength training, muscle gain and strength endurance. Whether you are just starting off or need some help getting to the next level of your journey we are here to get the job done.
We specialize in one on one or one on two personal training sessions and each program will be custom made to suit individual fitness goals of our clients

```html
<!DOCTYPE html>
<html lang="en">
<head>
<meta charset="utf-8">
<title>Pulse &amp; Stride – Business Card</title>
<link rel="stylesheet" href="https://fonts.googleapis.com/css2?family=Oswald:wght@500;700&family=Lato:wght@400;700&display=swap">
<style>
  :root {
    --bg: #1c1c1e;
    --purple-light: #a862ab;
    --purple-dark: #6f45a0;
    --ink: #141414;
    --paper: #ffffff;
    --accent: #8a52a8;
  }
  * { margin: 0; padding: 0; box-sizing: border-box; }
  html, body { width: 1200px; height: 1015px; overflow: hidden; background: var(--bg); }
  .canvas {
    width: 1200px; height: 1015px;
    display: flex; flex-direction: column; align-items: center; justify-content: center; gap: 44px;
  }
  .card {
    position: relative; width: 760px; height: 434px;
    background: var(--paper); overflow: hidden;
    box-shadow: 0 18px 40px rgba(0,0,0,.55);
  }
  .card svg.waves { position: absolute; inset: 0; }
  .brand { position: absolute; }
  .brand-name {
    display: flex; align-items: center; gap: 10px;
    font-family: "Oswald", sans-serif; font-weight: 700; font-size: 40px;
    letter-spacing: 1px; color: var(--ink); line-height: 1; text-transform: uppercase;
    white-space: nowrap;
  }
  .brand-dot { width: 20px; height: 20px; border-radius: 50%; background: var(--accent); flex: none; }
  .brand-tagline {
    margin-top: 8px; margin-left: 30px;
    font-family: "Oswald", sans-serif; font-weight: 500; font-size: 11px;
    letter-spacing: 1.5px; color: var(--accent); text-transform: uppercase; white-space: nowrap;
  }
  /* front */
  .card-front .brand { right: 40px; top: 205px; }
  .services { position: absolute; left: 58px; top: 46px; color: var(--paper); font-family: "Oswald", sans-serif; }
  .services h2 { font-weight: 700; font-size: 32px; letter-spacing: .5px; text-transform: uppercase; margin-bottom: 6px; }
  .services ul { list-style: none; }
  .services li {
    display: flex; align-items: center; gap: 10px;
    font-weight: 500; font-size: 18px; line-height: 1.4; text-transform: uppercase; margin-left: 20px;
  }
  .services li::before { content: ""; width: 9px; height: 9px; border-radius: 50%; background: var(--paper); }
  /* back */
  .card-back .brand { left: 60px; top: 110px; }
  .person { position: absolute; right: 50px; top: 22px; text-align: right; }
  .person-name { font-family: "Oswald", sans-serif; font-weight: 700; font-size: 34px; color: var(--accent); text-transform: uppercase; line-height: 1.05; }
  .person-role { font-family: "Lato", sans-serif; font-size: 19px; color: var(--ink); }
  .contacts { position: absolute; right: 44px; top: 205px; list-style: none; color: var(--paper); font-family: "Lato", sans-serif; font-size: 19px; text-align: right; }
  .contacts li { display: flex; justify-content: flex-end; align-items: flex-start; gap: 10px; line-height: 1.45; }
  .contacts svg { width: 18px; height: 18px; margin-top: 4px; flex: none; }
  .contacts .address { margin-top: 6px; }
</style>
</head>
<body>
<main class="canvas">

  <section class="card card-front" aria-label="Card front">
    <svg class="waves" viewBox="0 0 760 434" aria-hidden="true">
      <defs>
        <linearGradient id="purpleFront" x1="0" y1="0" x2="1" y2="1">
          <stop offset="0" stop-color="var(--purple-light)"/>
          <stop offset="1" stop-color="var(--purple-dark)"/>
        </linearGradient>
      </defs>
      <rect width="760" height="434" fill="url(#purpleFront)"/>
      <path transform="translate(0,-18)" d="M0,360 C200,350 300,300 370,220 C450,130 560,90 760,84" fill="none" stroke="var(--paper)" stroke-width="4"/>
      <path d="M0,434 V360 C200,350 300,300 370,220 C450,130 560,90 760,84 V434 Z" fill="var(--paper)"/>
      <path d="M260,318 C310,290 340,260 370,220 C450,130 560,90 760,84" fill="none" stroke="var(--ink)" stroke-width="7"/>
    </svg>
    <div class="services">
      <h2>Specialize in</h2>
      <ul>
        <li>Weight loss &amp; conditioning</li>
        <li>Strength training</li>
        <li>Muscle gain</li>
        <li>Strength endurance</li>
      </ul>
    </div>
    <div class="brand">
      <div class="brand-name"><span class="brand-dot"></span>Pulse &amp; Stride</div>
      <div class="brand-tagline">Personal training. Nutrition. Motivation</div>
    </div>
  </section>

  <section class="card card-back" aria-label="Card back">
    <svg class="waves" viewBox="0 0 760 434" aria-hidden="true">
      <defs>
        <linearGradient id="purpleBack" x1="0" y1="0" x2="1" y2="1">
          <stop offset="0" stop-color="var(--purple-light)"/>
          <stop offset="1" stop-color="var(--purple-dark)"/>
        </linearGradient>
      </defs>
      <path transform="translate(0,-14)" d="M0,380 C260,375 360,330 440,240 C520,150 600,112 760,110" fill="none" stroke="var(--ink)" stroke-width="7"/>
      <path d="M0,434 V380 C260,375 360,330 440,240 C520,150 600,112 760,110 V434 Z" fill="url(#purpleBack)"/>
      <path transform="translate(0,14)" d="M0,380 C260,375 360,330 440,240 C520,150 600,112 760,110" fill="none" stroke="var(--paper)" stroke-width="4"/>
    </svg>
    <div class="person">
      <div class="person-name">Marcus Reed</div>
      <div class="person-role">Managing Director</div>
    </div>
    <div class="brand">
      <div class="brand-name"><span class="brand-dot"></span>Pulse &amp; Stride</div>
      <div class="brand-tagline">Personal training. Nutrition. Motivation</div>
    </div>
    <ul class="contacts">
      <li>055-210 384 617
        <svg viewBox="0 0 24 24"><path d="M6.6 10.8a15 15 0 0 0 6.6 6.6l2.2-2.2a1 1 0 0 1 1-.25 11.4 11.4 0 0 0 3.6.57 1 1 0 0 1 1 1V20a1 1 0 0 1-1 1A17 17 0 0 1 3 4a1 1 0 0 1 1-1h3.5a1 1 0 0 1 1 1c0 1.250.2 2.45.57 3.57a1 1 0 0 1-.25 1z" fill="var(--paper)"/></svg></li>
      <li>hello@pulsestride.fit
        <svg viewBox="0 0 24 24"><rect x="2" y="5" width="20" height="14" rx="1.5" fill="var(--paper)"/><path d="M3 6l9 7 9-7" fill="none" stroke="var(--purple-dark)" stroke-width="1.6"/></svg></li>
      <li>www.pulsestride.fit
        <svg viewBox="0 0 24 24" fill="none" stroke="var(--paper)" stroke-width="1.8"><circle cx="12" cy="12" r="9.5"/><ellipse cx="12" cy="12" rx="4" ry="9.5"/><path d="M2.5 12h19M4 7h16M4 17h16"/></svg></li>
      <li class="address">88 Harbour Lane<br>Westfield, 30714
        <svg viewBox="0 0 24 24"><path d="M12 2a7 7 0 0 0-7 7c0 5 7 13 7 13s7-8 7-13a7 7 0 0 0-7-7z" fill="var(--paper)"/><circle cx="12" cy="9" r="2.6" fill="var(--purple-dark)"/></svg></li>
    </ul>
  </section>

</main>
</body>
</html>
```